New Business Card Design Project

We require a business card design for Vexalund, a newly established Indian company.
Our focus is on the development, manufacturing, and export of a diverse array of pharmaceutical products on a global scale. The card should convey a professional appearance, as our primary markets are in Africa, China, and Southeast Asian nations.
We envision a two-sided business card, with the reverse side dedicated to a logo set against a solid color or an elegantly designed pattern. The corners should be rounded. We would appreciate seeing both horizontal and vertical design options. We trust the designer to utilize their expertise in creating this design.

The content for the business card is included in the attached Word file.

Target Market(s)

Our primary markets are in Africa, China, and Southeast Asian, Latin America, Maldives, Sri Lanka

Industry/Entity Type

Pharmaceutical Manufacturing and Export

Contact Information for Business Card

Colors

Designer to choose colors to be used in the design.

Requirements
Must have
• The reverse side of the business card features solely the logo along with the tagline, "Cures for Living."
Should not have
• The logo should not exceed two instances, encompassing both the front and back sides of the card.

```html
<!DOCTYPE html>
<html lang="en">
<head>
<meta charset="utf-8">
<title>Vexalund Business Card</title>
<link rel="stylesheet" href="https://fonts.googleapis.com/css2?family=Open+Sans:wght@300;400;700&family=Poppins:wght@400;600&display=swap">
<style>
  :root {
    --backdrop: #222222;
    --paper: #f1f1f2;
    --brand-blue: #2ea8df;
    --brand-coral: #f0644d;
    --ink: #1c1c1c;
  }
  * { margin: 0; padding: 0; box-sizing: border-box; }
  html, body {
    width: 1200px;
    height: 711px;
    overflow: hidden;
    background: var(--backdrop);
  }
  .canvas {
    position: relative;
    width: 1200px;
    height: 711px;
  }
  .card {
    position: absolute;
    left: 341px;
    width: 518px;
    height: 296px;
    border-radius: 22px;
    background: var(--paper);
    overflow: hidden;
  }
  .card--reverse { top: 45px; }
  .card--front { top: 370px; }

  .brand-name {
    position: absolute;
    font-family: "Poppins", sans-serif;
    font-weight: 600;
    color: var(--brand-blue);
    line-height: 1;
    white-space: nowrap;
    letter-spacing: -0.5px;
  }
  .brand-dot {
    position: absolute;
    border-radius: 50%;
    background: var(--brand-coral);
  }

  /* reverse side */
  .card--reverse .brand-dot {
    width: 54px; height: 54px;
    left: 232px; top: 84px;
  }
  .card--reverse .brand-name {
    left: 0; right: 0; top: 178px;
    text-align: center;
    font-size: 52px;
  }
  .tagline {
    position: absolute;
    left: 0; right: 0; top: 262px;
    text-align: center;
    font-family: "Poppins", sans-serif;
    font-size: 13px;
    color: var(--ink);
  }

  /* front side */
  .card--front .brand-dot {
    width: 38px; height: 38px;
    left: 97px; top: 114px;
  }
  .card--front .brand-name {
    left: 36px; width: 160px; top: 176px;
    text-align: center;
    font-size: 32px;
  }
  .divider {
    position: absolute;
    left: 259px; top: 49px;
    width: 1px; height: 199px;
    background: var(--brand-coral);
  }
  .contact {
    position: absolute;
    left: 303px; top: 70px;
    font-family: "Open Sans", sans-serif;
    color: var(--ink);
  }
  .contact__name {
    font-size: 22px;
    font-weight: 300;
    color: var(--brand-blue);
    line-height: 28px;
    white-space: nowrap;
  }
  .contact__name strong { font-weight: 700; }
  .contact__role {
    font-size: 13.5px;
    line-height: 18px;
  }
  .contact__address {
    margin-top: 10px;
    font-size: 12.5px;
    line-height: 17.5px;
    font-style: normal;
  }
  .contact__list {
    list-style: none;
    margin-top: 14px;
    font-size: 12.5px;
  }
  .contact__list li {
    display: flex;
    align-items: center;
    height: 17.5px;
  }
  .contact__list svg {
    width: 12px; height: 12px;
    margin-right: 8px;
    flex: none;
  }
</style>
</head>
<body>
<main class="canvas">
  <section class="card card--reverse" aria-label="Card reverse">
    <span class="brand-dot"></span>
    <span class="brand-name">Vexalund</span>
    <p class="tagline">Cures for Living.</p>
  </section>

  <section class="card card--front" aria-label="Card front">
    <span class="brand-dot"></span>
    <span class="brand-name">Vexalund</span>
    <span class="divider"></span>
    <div class="contact">
      <p class="contact__name"><strong>Arjun</strong> K. Velkar</p>
      <p class="contact__role">CEO</p>
      <address class="contact__address">14, Sundar Nagar,<br>Ranvale, 440118, India</address>
      <ul class="contact__list">
        <li>
          <svg viewBox="0 0 12 12" aria-hidden="true"><rect x="2.5" y="0.5" width="7" height="11" rx="1" fill="none" stroke="var(--brand-coral)" stroke-width="1.2"/><line x1="5" y1="10" x2="7" y2="10" stroke="var(--brand-coral)" stroke-width="1"/></svg>
          +919 555012345
        </li>
        <li>
          <svg viewBox="0 0 12 12" aria-hidden="true"><circle cx="6" cy="6" r="5.5" fill="var(--brand-blue)"/><ellipse cx="6" cy="6" rx="2.3" ry="5.5" fill="none" stroke="#fff" stroke-width="0.8"/><line x1="0.5" y1="6" x2="11.5" y2="6" stroke="#fff" stroke-width="0.8"/></svg>
          www.vexalund.com
        </li>
        <li>
          <svg viewBox="0 0 12 12" aria-hidden="true"><rect x="0.5" y="2.5" width="11" height="8.5" fill="var(--brand-coral)"/><polyline points="0.5,2.5 6,7 11.5,2.5" fill="none" stroke="#fff" stroke-width="0.9"/></svg>
          akvelkar@vexalund.com
        </li>
      </ul>
    </div>
  </section>
</main>
</body>
</html>
```